Website for a company offering full serivce charging solutions for electric cars

The company "tanu-werk" (english: "tanu-works") offering all-in-one-solutions for charging infrastructure for electric mobility.

There are four products:
1- Wallboxes for single-family homes
2- Solutions for property devloper/-management for property parking space
3- All-in-one-charging solution for municipalities/communities
4- Solutions for tourism/hotels/holiday appartments

The Website structure:
1. Main Page
2.1. Product Page Single Homes
2.2. Product Page Property Management / Parking
2.3. Product Page Municipality
2.4. Product Page Tourism
3. Contact Form / Request for information
4. Imprint / Legal

The Website should be built on Wordpress with a powerful possibility to simply add/modify specific landing pages.

We would like you to implement the website later and also maintain it if possible, but we would be able to do minor modifications by ourselfs (for A/B-Testing)

The website should be clear and simple, easy to understand.
Target group is mainly B2C without deeper knowledge of that topic.

It should suggest, that we will provide a very simple way to get the charging infrastructure done.

We need a contact form, maybe we will use Hubspot later.

Attached you will find a draft of the main page and a landing page (for 2.2) - it is just the content, please ignore the design. We would love to let you create a suitable design.
Also you will find some drafts a bit different for the same story.

I added also a few stock photos, but they don't need to be used! If you have better ideas, you are welcome!

Industry/Entity Type

Charging/Electric mobility

Number of Pages Required

2 page

Font styles to use
Sans Serif

Requirements
Must have
• Based on Wordpress, and the designer should be able to implement it on Wordpress on a later step

```html
<!DOCTYPE html>
<html lang="de">
<head>
<meta charset="utf-8">
<title>tanu-werk – Ladelösungen für E-Fahrzeuge</title>
<link rel="stylesheet" href="https://fonts.googleapis.com/css2?family=Saira:wght@300;400;600;700&family=Arimo:wght@400;700&display=swap">
<style>
:root{
  --bg:#121a28;
  --bg-alt:#142238;
  --pink:#e5218b;
  --purple:#8e3fd8;
  --white:#ffffff;
  --text:#dfe3ec;
  --muted:#9aa1ae;
}
*{box-sizing:border-box;margin:0;padding:0}
html,body{width:1200px;height:4222px;overflow:hidden}
body{background:var(--bg);color:var(--white);font-family:"Arimo",Arial,sans-serif;position:relative}
.abs{position:absolute}
.head-font{font-family:"Saira",Arial,sans-serif}

/* header */
.site-header{left:0;top:0;width:1200px;height:86px}
.brand{left:102px;top:18px;display:flex;align-items:center;gap:10px}
.brand-dot{width:34px;height:34px;border-radius:50%;background:var(--pink)}
.brand-name{font-family:"Saira",sans-serif;font-weight:600;font-size:26px;line-height:26px;color:var(--white)}
.brand-tag{font-size:13px;color:var(--text);margin-top:2px}
.nav a{position:absolute;top:28px;font-size:14px;color:var(--white);text-decoration:none;transform:translateX(-50%);white-space:nowrap}
.nav a.active::after{content:"";position:absolute;left:0;right:0;bottom:-14px;height:2px;background:var(--pink)}
.btn-pill{border-radius:30px;background:linear-gradient(90deg,var(--purple),var(--pink));color:#fff;font-weight:700;font-size:15px;display:flex;align-items:center;justify-content:center;text-decoration:none}
.nav-cta{left:947px;top:20px;width:146px;height:41px}

/* hero */
.hero-visual{left:0;top:87px;width:1180px;height:603px;border-radius:0 330px 330px 0;background:radial-gradient(ellipse at 62% 62%,#9fb2c6 0%,#3f5a7a 18%,#23324b 42%,#141d2d 75%);}
.hero-title{left:116px;top:214px;font-family:"Saira",sans-serif;font-size:60px;line-height:56px;color:#fff}
.hero-title b{font-weight:700}
.hero-title span{font-weight:300}
.hero-text{left:120px;top:350px;font-size:20.5px;line-height:30px;color:var(--text);width:480px}
.hero-cta{left:115px;top:437px;width:193px;height:51px;font-size:16px}

/* intro */
.bolt{width:28px;height:42px}
.intro-lead{left:210px;top:776px;width:784px;text-align:center;font-size:22px;line-height:33px;font-weight:700}
.intro-copy{left:165px;top:894px;width:870px;text-align:center;font-size:16.5px;line-height:26px;color:var(--text)}
.intro-visual{left:92px;top:1000px;width:1001px;height:262px;border-radius:24px;background:radial-gradient(ellipse at 50% 60%,#3d6fd1 0%,#1d2f63 30%,#151f3a 65%,var(--bg) 100%)}
.question{left:0;top:1336px;width:1200px;text-align:center;font-family:"Saira",sans-serif;font-size:30px;line-height:35px}
.question b{font-weight:600}
.question span{font-weight:300}

/* sections */
.sec-title{font-family:"Saira",sans-serif;font-size:34px;line-height:40px;font-weight:300;color:#fff}
.sec-title b{font-weight:600;color:var(--pink)}
.sec-rule{width:50px;height:3px;background:#fff}
.check-list{list-style:none}
.check-list li{position:relative;padding-left:18px;color:var(--text)}
.check-list li::before{content:"";position:absolute;left:1px;top:5px;width:6px;height:6px;border-right:2px solid var(--pink);border-top:2px solid var(--pink);transform:rotate(45deg)}
.check-list.white li::before{border-color:#fff}

.private-visual{left:98px;top:1518px;width:477px;height:396px;border-radius:50px 50px 0 50px;background:linear-gradient(135deg,#cfe7ee 0%,#6fa6b8 35%,#2c4258 70%,#151c29 100%)}
.private-list{left:624px;top:1585px;width:510px}
.private-list li{padding-left:0;font-size:13px;line-height:15px;margin-bottom:9px}
.private-list li::before{display:none}

.business-band{left:0;top:2024px;width:1200px;height:677px;background:var(--bg-alt)}
.business-list{font-size:13px;line-height:17px;font-weight:700;color:#fff}
.business-list li{color:#fff;margin-bottom:9px}
.business-list .sub{list-style:none;margin:8px 0 4px 12px;font-weight:400}
.business-list .sub li{margin-bottom:2px}
.business-visual{left:587px;top:2360px;width:613px;height:341px;border-radius:200px 0 0 0;background:radial-gradient(ellipse at 40% 40%,#4f6fe0 0%,#283d8f 30%,#172749 65%,var(--bg-alt) 100%)}

.community-visual{left:115px;top:2786px;width:442px;height:566px;border-radius:30px;background:radial-gradient(ellipse at 50% 35%,#7fb3ff 0%,#3e5ed0 30%,#20305e 60%,var(--bg) 100%)}
.community-list{left:628px;top:2868px;width:520px}
.community-list li{font-size:13.5px;line-height:17px;margin-bottom:10.5px}

/* contact */
.contact-band{left:13px;top:3442px;width:1187px;height:537px;border-radius:270px 0 0 270px;background:linear-gradient(100deg,#7a2fd0 0%,#9a2bb8 40%,#d21f95 75%,#e81f82 100%)}
.contact-title{left:0;top:3540px;width:1200px;text-align:center;font-family:"Saira",sans-serif;font-size:38px;line-height:44px;font-weight:300}
.contact-title b{font-weight:700}
.field{background:#fff;border-radius:3px;color:#555;font-size:13px;display:flex;align-items:center;gap:10px;padding:0 18px}
.field svg{width:16px;height:16px;flex:none}
.field.message{align-items:flex-start;padding-top:16px}
.submit{left:511px;top:3830px;width:194px;height:50px;background:#141d33;color:#fff;font-weight:700;font-size:16px;display:flex;align-items:center;justify-content:center;border-radius:3px}

/* footer */
.footer-brand{left:0;top:4012px;width:1200px;text-align:center;font-family:"Saira",sans-serif;font-weight:600;font-size:30px;color:#fff}
.footer-brand i{display:inline-block;width:22px;height:22px;border-radius:50%;background:var(--pink);margin-right:10px;vertical-align:-2px}
.footer-nav a{position:absolute;top:4082px;font-size:14px;color:#fff;text-decoration:none;transform:translateX(-50%);white-space:nowrap}
.copyright{left:0;top:4118px;width:1200px;text-align:center;font-size:13px;color:var(--muted)}
.social{top:4160px;width:31px;height:31px;border-radius:50%;background:linear-gradient(135deg,var(--purple),var(--pink))}
</style>
</head>
<body>

<header class="site-header abs">
  <div class="brand abs">
    <span class="brand-dot"></span>
    <div>
      <div class="brand-name">tanu-werk.de</div>
      <div class="brand-tag">einfach mehr als laden</div>
    </div>
  </div>
  <nav class="nav">
    <a class="active" style="left:467px">LÖSUNGEN</a>
    <a style="left:613px">UNTERNEHMEN</a>
    <a style="left:752px">SERVICES</a>
    <a style="left:870px">KARRIERE</a>
  </nav>
  <a class="btn-pill nav-cta abs">KONTAKT</a>
</header>

<section>
  <div class="hero-visual abs" role="img" aria-label="Weißes Elektroauto in dunkler Garage, mit leuchtendem Kabel an einer Wandladestation"></div>
  <h1 class="hero-title abs"><b>tanu-werk ist</b><br><span>Ihr Partner</span></h1>
  <p class="hero-text abs">wenn das Laden nicht nur einfach, sondern die Umsetzung auch aus einer Hand kommen soll</p>
  <a class="btn-pill hero-cta abs">LEARN MORE</a>
</section>

<section>
  <svg class="bolt abs" style="left:588px;top:728px" viewBox="0 0 28 42" fill="none" stroke="#e5218b" stroke-width="2" stroke-linejoin="round"><path d="M17 2 4 24h10l-3 16 13-24H14z"/></svg>
  <p class="intro-lead abs">Wir&nbsp; bieten Lösungen sowohl für Privatkunden, Geschäftskunden als auch Kommunen an, die schnell, fair und ohne Eigenleistung zu einer smarten Ladelösung für E-Fahrzeuge kommen möchten.</p>
  <p class="intro-copy abs">Von der Beratung, über die Installation, Inbetriebnahme bis zur Abrechnung und Wartung bekommen Sie bei tanu-werk alles aus einer Hand. Auf Wunsch vermieten wir auch die Ladetechnik und übernehmen im gewerblichen Bereich die direkte Abrechnung mit dem Nutzer. Für Kommunen bieten wir den kostenfreien Full-Service an und beteiligen die Gemeinden an der Nutzung der Infrastruktur.</p>
  <div class="intro-visual abs" role="img" aria-label="Silhouette eines Elektroautos mit leuchtender Batterie neben einer Ladesäule"></div>
  <svg class="abs" style="left:615px;top:1210px" width="2" height="80"><line x1="1" y1="0" x2="1" y2="80" stroke="#9aa1ae" stroke-width="1"/></svg>
  <svg class="bolt abs" style="left:602px;top:1282px" viewBox="0 0 28 42" fill="none" stroke="#e5218b" stroke-width="2" stroke-linejoin="round"><path d="M17 2 4 24h10l-3 16 13-24H14z"/></svg>
  <h2 class="question abs"><b>FRAGEN SIE UNS NACH DER AUF IHRE INDIVIDUELLEN</b><br><span>BEDÜRFNISSE ZUGESCHNITTENEN LÖSUNG:</span></h2>
</section>

<section>
  <div class="private-visual abs" role="img" aria-label="Nahaufnahme eines EV-Ladesteckers in der Ladebuchse eines Fahrzeugs"></div>
  <h2 class="sec-title abs" style="left:624px;top:1518px">ALS <b>PRIVATKUNDE</b></h2>
  <div class="sec-rule abs" style="left:624px;top:1564px"></div>
  <ul class="check-list private-list abs">
    <li>Bestandsanalyse mit umfangreicher Beratung über die Möglichkeiten der Umsetzung</li>
    <li>Prüfung und Übernahme der Anmeldung verfügbarer Fördermöglichkeiten</li>
    <li>Auswahl an smarten Wallbox Lösungen, passend für Ihr Fahrzeug und Ihre Bedürfnisse</li>
    <li>Installation inkl. aller notwendigen Materialien und Tätigkeiten (Durchbrüche, Erdarbeiten, etc.)</li>
    <li>Inbetriebnahme und Einweisung in die Ladetechnik</li>
    <li>Jährlich technische Wartung nach DGUV3</li>
    <li>Reparaturservice, unter Berücksichtigung der geltenden Garantie Ansprüche</li>
    <li>Installation inkl. aller notwendigen Materialien und Tätigkeiten (Durchbrüche, Erdarbeiten, etc.</li>
    <li>Inbetriebnahme und Einweisung in die Ladetechnik</li>
    <li>Jährlich technische Wartung nach DGUV3</li>
    <li>Reparaturservice, unter Berücksichtigung der geltenden Garantie Ansprüche</li>
  </ul>
</section>

<section>
  <div class="business-band abs"></div>
  <div class="business-visual abs" role="img" aria-label="Leuchtender Ladestecker vor blauen Schaltkreislinien"></div>
  <h2 class="sec-title abs" style="left:0;top:2082px;width:1210px;text-align:center">ALS <b>GESCHÄFTSKUNDE</b></h2>
  <div class="sec-rule abs" style="left:578px;top:2130px"></div>
  <ul class="check-list white business-list abs" style="left:120px;top:2186px;width:480px">
    <li>Durchführung einer individuellen Bedarfsanalyse inkl. Ermittlung der</li>
    <li>Anforderungen für:
      <ul class="check-list white sub">
        <li>Haus- und Immobilienverwaltungen</li>
        <li>Dienstleistungs- und Handelsunternehmen</li>
        <li>Hotel und Beherbergungsbetriebe</li>
        <li>Parkraum- und Parkhausbetreiber</li>
        <li>Tourismus, Sport- und Freizeiteinrichtungen</li>
      </ul>
    </li>
    <li>Planung und Projektierung des Installationsaufwands inkl.</li>
    <li style="margin-bottom:18px">Materialverbrauch</li>
    <li style="margin-bottom:18px">Leasing oder Kauf der Hardware</li>
    <li>Normgerechte Installation der Ladeinfrastruktur inkl. Durchbruch-,</li>
    <li style="margin-bottom:18px">Brandschutz- und Erdarbeiten</li>
    <li style="line-height:26px;margin-bottom:8px">Unterstützung bei der mtl. Nutzungsabrechnung und Einbindung in Ihre vorhandene Abrechnungssysteme</li>
    <li>ODER direkte Abrechnung mit den Nutzern</li>
  </ul>
  <ul class="check-list white business-list abs" style="left:644px;top:2193px;width:480px">
    <li style="margin-bottom:17px">Bei Bestandsbauten Integration der Ladeinfrastruktur in die</li>
    <li style="margin-bottom:17px">Gebäudesystemtechnik und ggf. Anpassung des Netzanschlusses</li>
    <li style="margin-bottom:17px">Inbetriebnahme der Anlage inkl. Prüf- und Messprotokollen</li>
    <li style="margin-bottom:17px">Wiederkehrende technische Prüfung der Anlage nach DGUV 3</li>
    <li>Austausch und Reparatur Service</li>
  </ul>
</section>

<section>
  <div class="community-visual abs" role="img" aria-label="Hand hält ein Smartphone, darüber ein leuchtendes Elektroauto mit Ladestecker"></div>
  <h2 class="sec-title abs" style="left:626px;top:2793px">ALS <b>KOMMUNE</b></h2>
  <ul class="check-list community-list abs">
    <li>Konzeptionierung möglicher Ladeinfrastrukturen innerhalb Ihrer Gemeinde</li>
    <li>Planung und Projektsteuerung inkl. sämtlicher behördlicher Genehmigungsverfahren und Beantragung von Fördermitteln</li>
    <li>Fachgerechte Innstallation und Inbetriebnahme</li>
    <li>Regelmäßige Wartung gemäß Vorschrif</li>
    <li>Reparatur und Kundenservice</li>
    <li>Direkte Abrechnung mit dem Nutzer</li>
    <li>Beteiligung der Gemeinde am Umsatz</li>
    <li>Möglichkeit der Integration von Bonusprogrammen, mit denen der lokale Einzelhandel beworben wird</li>
    <li>von Fördermitteln<br>Fachgerechte Installation und Inbetriebnahme</li>
    <li>Regelmäßige Wartung gemäß Vorschrif</li>
    <li>Reparatur und Kundenservice</li>
    <li>Direkte Abrechnung mit dem Nutzer</li>
    <li>Beteiligung der Gemeinde am Umsatz</li>
    <li>Möglichkeit der Integration von Bonusprogrammen, mit denen der lokale Einzelhandel beworben wird</li>
  </ul>
</section>

<section>
  <div class="contact-band abs" role="img" aria-label="Violett-pinker Hintergrund mit schemenhaftem Auto an einer Ladestation"></div>
  <h2 class="contact-title abs">CONTACT <b>US</b></h2>
  <div class="sec-rule abs" style="left:566px;top:3591px;width:68px"></div>
  <div class="field abs" style="left:198px;top:3630px;width:404px;height:50px">
    <svg viewBox="0 0 16 16" fill="none" stroke="#888" stroke-width="1.3"><circle cx="8" cy="5" r="3"/><path d="M2 15c0-3.5 2.7-5.5 6-5.5s6 2 6 5.5"/></svg>Your Name*</div>
  <div class="field abs" style="left:198px;top:3691px;width:404px;height:51px">
    <svg viewBox="0 0 16 16" fill="none" stroke="#888" stroke-width="1.3"><rect x="1" y="3" width="14" height="10"/><path d="M1 3l7 6 7-6"/></svg>Email address*</div>
  <div class="field abs" style="left:198px;top:3753px;width:404px;height:51px">
    <svg viewBox="0 0 16 16" fill="none" stroke="#888" stroke-width="1.3"><path d="M4 1l3 3-2 2c1 2 3 4 5 5l2-2 3 3-2 3C7 15 1 9 1 3z"/></svg>Phone number*</div>
  <div class="field message abs" style="left:610px;top:3630px;width:405px;height:174px">Leave Message</div>
  <div class="submit abs">SUBMIT NOW</div>
</section>

<footer>
  <div class="footer-brand abs"><i></i>tanu-werk</div>
  <nav class="footer-nav">
    <a style="left:226px">AGB</a>
    <a style="left:393px">DATENSCHUTZERKLÄRUNG</a>
    <a style="left:593px">IMPRESSUM</a>
    <a style="left:726px">KONTAKT</a>
    <a style="left:852px">KARRIERE</a>
    <a style="left:964px">FAQS</a>
  </nav>
  <p class="copyright abs">© 2022 tanu-werk GmbH |&nbsp; All Right Reserved</p>
  <span class="social abs" style="left:524px" aria-label="Soziales Netzwerk 1"></span>
  <span class="social abs" style="left:562px" aria-label="Soziales Netzwerk 2"></span>
  <span class="social abs" style="left:600px" aria-label="Soziales Netzwerk 3"></span>
  <span class="social abs" style="left:637px" aria-label="Soziales Netzwerk 4"></span>
</footer>

</body>
</html>
```